Surya Namaskar/Sun salutation theme based 12 months desk calendar for 2016 for an indian company

1. We are a corporate support services provider, providing services in Security Management, Fire Safety Management, facility management & HR Services based out of India. pls check website: www.brelvanta.co.in
2. Need a complete 12 months desk calendar design layout for 2016 including introductory page & end page,which can then be given for printing straightaway. The calendar should be so designed that when we open any month on the front side, the back side should also give out just the same month dates layout with space to note down any important work on a date etc..All important indian festivals, gazetted hoildays should be mentioned. Any information required can be provided by us
3. Since we give this calendars as part of new year gifts, our calendar has to compete for client desk space with other calendars, it must really be very sophisticated, sleek and attractive
4. Company logo, company contact details, website details and company works must be included in the calendar but in subtle, unobtrusive way. Few details like company logo etc, can be there on all pages.Am uploading some details, rest can be taken from the website, or can be provided
5. Calendar size should be aprx 17 cm * 17 cm including the space needed for spiral. Format should be CDR Ver13 or PDF
6. Theme: Surya Namaskar poses/Sun Salutation poses. These are twelve yoga poses, prescribed for mind /body rejuvenation. Poses 1-12 should be on months Jan16 to Dec 16. A very brief writeup on the same including the relevant mantras may also be included on the page
7. Any query , please mail to rohan.mehtra@brelvanta.co.in

Target Market(s)

corporate middle & senior management MNC clients

Industry/Entity Type

Security

Requirements
Must have
• 1.company logos/contact & website details/company works with related photographs.
• 2. surya namaskar poses with a very small brief/health benefit on poses/related mantras
• 3. Indian gazetted holidays & festivals earmarked
• 4. recommendation on the printing paper type & quality/colour of cardboard base & spiral binding
• 5. Attractive Top Introduction page & end page
Nice to have
• 1. photos of the company works
• 2. End page may be used for giving company details in details
• 3. Company logo on each page
• 4. The calendar goes to a variety of corporate clients including hotels, hospitals, shopping malls, manufacturing sector, clubs etc..just for info
• 5. Related photos/same model in all months
• 6. Beautiful Female models in poses
• 7. target audience : 95% male; majority age group: 35-55; middle & senior management
• However, very receptive to any new ideas. The designer has full liberty from our side. The final parameter is that the calendar should be so attractive that it can defeat any other desk calendar competition and win that one spot on the desk
• Any queries/details required, pls mail to rohan.mehtra@brelvanta.co.in
Should not have
• Religious overtones

```html
<!DOCTYPE html>
<html lang="en">
<head>
<meta charset="UTF-8">
<title>March – Sun Salutation Desk Calendar</title>
<link rel="stylesheet" href="https://fonts.googleapis.com/css2?family=Playfair+Display:ital,wght@1,900&family=Cormorant+Garamond:ital,wght@1,500&family=Jost:wght@500;600&display=swap">
<style>
  :root {
    --cream: #efe8da;
    --teal: #2b6f63;
    --sun-yellow: #f6c21c;
    --sun-orange: #ef8a17;
    --ink: #141414;
    --sunday-red: #c0272d;
    --cell-border: #2a2a2a;
    --wall-light: #f4f0ea;
    --wall-mid: #e9e1d5;
    --wall-shade: #d6cbbb;
    --figure-slate: #8b8797;
    --leaf-green: #8fa57a;
  }
  * { margin: 0; padding: 0; box-sizing: border-box; }
  html, body { width: 1200px; height: 1200px; overflow: hidden; background: var(--cream); }
  .calendar-page { position: relative; width: 1200px; height: 1200px; background: var(--cream); overflow: hidden; }

  .pose-photo {
    position: absolute; left: 0; top: 0; width: 1200px; height: 660px;
    background:
      linear-gradient(180deg, rgba(143,165,122,0.35) 0%, rgba(143,165,122,0) 14%),
      linear-gradient(100deg, var(--wall-light) 0%, var(--wall-mid) 38%, var(--figure-slate) 66%, var(--wall-mid) 86%, var(--wall-light) 100%),
      var(--wall-mid);
    background-blend-mode: normal, normal;
  }
  .pose-photo::after {
    content: ""; position: absolute; left: 0; right: 0; bottom: 0; height: 120px;
    background: linear-gradient(180deg, rgba(214,203,187,0) 0%, var(--wall-shade) 100%);
  }

  .mantra-panel {
    position: absolute; left: 0; top: 117px; width: 488px; height: 156px;
    background: rgba(255,255,255,0.6);
    border-radius: 0 78px 78px 0;
  }
  .mantra-title {
    position: absolute; left: 49px; top: 130px;
    font-family: "Playfair Display", Georgia, serif; font-style: italic; font-weight: 900;
    font-size: 44px; line-height: 57px; color: var(--ink); white-space: nowrap;
  }
  .mantra-meaning {
    position: absolute; left: 49px; top: 298px;
    font-family: "Cormorant Garamond", Georgia, serif; font-style: italic; font-weight: 500;
    font-size: 47px; line-height: 55px; color: var(--ink); white-space: nowrap;
  }

  .wave-band { position: absolute; left: 0; top: 0; width: 1200px; height: 1200px; }

  .month-name {
    position: absolute; left: 295px; top: 650px; width: 160px; text-align: center;
    font-family: "Jost", sans-serif; font-weight: 600; font-size: 36px; letter-spacing: 0.5px; color: var(--ink);
  }
  .weekdays { position: absolute; left: 72px; top: 704px; display: grid; grid-template-columns: repeat(7, 76px); column-gap: 12px; }
  .weekdays span { text-align: center; font-family: "Jost", sans-serif; font-weight: 600; font-size: 17px; color: var(--ink); }
  .weekdays .sun { color: var(--sunday-red); }

  .date-grid {
    position: absolute; left: 72px; top: 735px;
    display: grid; grid-template-columns: repeat(7, 76px); grid-auto-rows: 76px; gap: 12px;
  }
  .date-cell {
    border: 1.5px solid var(--cell-border);
    display: flex; align-items: center; justify-content: center;
    font-family: "Jost", sans-serif; font-weight: 500; font-size: 43px; color: var(--ink);
  }
  .date-cell.sunday { border-color: var(--sunday-red); color: var(--sunday-red); }

  .notes { position: absolute; left: 733px; top: 808px; width: 393px; }
  .notes span { display: block; height: 2px; background: var(--ink); margin-bottom: 86px; }
</style>
</head>
<body>
<main class="calendar-page">
  <div class="pose-photo" role="img" aria-label="Photograph of a woman in a low lunge Sun Salutation pose on a white mat in a sunlit courtyard with lattice windows and climbing plants"></div>

  <div class="mantra-panel"></div>
  <h1 class="mantra-title">Om Hroom<br>Suryaya Namah</h1>
  <p class="mantra-meaning">Prostration to Him<br>who induces activity.</p>

  <svg class="wave-band" viewBox="0 0 1200 1200" aria-hidden="true">
    <defs>
      <linearGradient id="sunSwoosh" x1="0" y1="1" x2="1" y2="0">
        <stop offset="0" stop-color="var(--sun-orange)"/>
        <stop offset="1" stop-color="var(--sun-yellow)"/>
      </linearGradient>
    </defs>
    <path d="M0,622 C250,602 600,612 930,600 C1050,590 1140,520 1200,430 L1200,665 C1050,690 820,695 640,662 C430,625 220,650 0,670 Z" fill="var(--teal)"/>
    <path d="M930,600 C1040,590 1140,500 1200,360 L1200,425 C1140,520 1050,592 930,600 Z" fill="url(#sunSwoosh)"/>
  </svg>

  <h2 class="month-name">MARCH</h2>
  <div class="weekdays">
    <span class="sun">SUN</span><span>MON</span><span>TUE</span><span>WED</span><span>THU</span><span>FRI</span><span>SAT</span>
  </div>

  <div class="date-grid">
    <div class="date-cell sunday"></div><div class="date-cell"></div><div class="date-cell">1</div><div class="date-cell">2</div><div class="date-cell">3</div><div class="date-cell">4</div><div class="date-cell">5</div>
    <div class="date-cell sunday">6</div><div class="date-cell">7</div><div class="date-cell">8</div><div class="date-cell">9</div><div class="date-cell">10</div><div class="date-cell">11</div><div class="date-cell">12</div>
    <div class="date-cell sunday">13</div><div class="date-cell">14</div><div class="date-cell">15</div><div class="date-cell">16</div><div class="date-cell">17</div><div class="date-cell">18</div><div class="date-cell">19</div>
    <div class="date-cell sunday">20</div><div class="date-cell">21</div><div class="date-cell">22</div><div class="date-cell">23</div><div class="date-cell">24</div><div class="date-cell">25</div><div class="date-cell">26</div>
    <div class="date-cell sunday">27</div><div class="date-cell">28</div><div class="date-cell">29</div><div class="date-cell">30</div><div class="date-cell">31</div><div class="date-cell"></div><div class="date-cell"></div>
  </div>

  <div class="notes"><span></span><span></span><span></span><span></span><span></span></div>
</main>
</body>
</html>
```